Corvana Tongue Works, LLC

We need a business card that includes information about our business and conveys a reliable business that provides document translation services and interpreters for a variety of corporate and individual clients. We want to come across as professional, reliable, yet approachable. It should include the following on one side:

ESL / ENL Language Classes, Private Lessons, and Online Tutors
PLEXA Training and Testing
Translating & Interpreting Services
Contact us about Over-the-Phone Interpreting in over 200 languages
24/7/365
www.corvanatongue.example

The other side should include (555) 481-3062

Rhoda Pelling, President
482 Garnet Ave., Ste. 219
Indianapolis, IN 40917

Please add USA as part of the address. Also, please add rmpelling@corvanatongueworks.example as the e-mail address. Thank you.

Target Market(s)

Business professionals, their families, the international community

Industry/Entity Type

Business

Contact Information for Business Card

24/7/365
www.corvanatongue.example

(555) 481-3062

Rhoda Pelling, President
482 Garnet Ave., Ste. 219
Indianapolis, IN 40917
USA

Font styles to use
Sans Serif

Colors

Designer to choose colors to be used in the design.

Requirements
Must have
• See project description
• e-mail address and web address
• Phone number
Nice to have
• a globe
• physical address
Should not have
• Should not have the same color scheme as other agencies in our market in Indiana unless it is blue and black. No purple or yellow.

```html
<!DOCTYPE html>
<html lang="en">
<head>
<meta charset="utf-8">
<title>Corvana Tongue Works, LLC – Business Card</title>
<link rel="stylesheet" href="https://fonts.googleapis.com/css2?family=Roboto:wght@400;500;700&display=swap">
<style>
  :root {
    --ink: #0b0b0c;
    --paper: #ffffff;
    --brand-blue: #2d95d6;
    --brand-blue-light: #5cb6ea;
    --stage: #4a4541;
    --card-shadow: rgba(0,0,0,0.45);
    --body-font: "Roboto", Arial, sans-serif;
  }
  * { box-sizing: border-box; margin: 0; padding: 0; }
  html, body { width: 1200px; height: 930px; overflow: hidden; }
  body { background: var(--stage); font-family: var(--body-font); position: relative; }

  .card {
    position: absolute;
    width: 560px;
    height: 320px;
    border-radius: 16px;
    overflow: hidden;
    box-shadow: 0 18px 40px var(--card-shadow);
  }

  /* ---------- Back side ---------- */
  .card--back { left: 90px; top: 90px; background: var(--ink); color: var(--paper); }
  .brand--back { position: absolute; left: 150px; top: 36px; display: flex; align-items: center; gap: 16px; }
  .brand-dot { width: 96px; height: 96px; border-radius: 50%; background: var(--brand-blue); flex: none; }
  .brand-name { font-weight: 500; font-size: 32px; line-height: 1.02; letter-spacing: 0.2px; }
  .brand--back .brand-name { color: var(--brand-blue); }
  .brand-name small { font-size: 13px; letter-spacing: 1px; }
  .services { position: absolute; left: 40px; right: 40px; top: 160px; text-align: center; }
  .rule { height: 2px; background: var(--brand-blue); margin: 0 10px; }
  .service-list { list-style: none; padding: 10px 0 12px; font-size: 15px; line-height: 1.38; font-weight: 500; }
  .contact-note { padding-top: 10px; font-size: 15px; line-height: 1.4; font-weight: 500; }

  /* ---------- Front side ---------- */
  .card--front { left: 550px; top: 500px; background: var(--paper); }
  .wave { position: absolute; inset: 0; width: 100%; height: 100%; }
  .brand--front { position: absolute; left: 34px; top: 80px; display: flex; align-items: center; gap: 12px; }
  .brand--front .brand-dot { width: 80px; height: 80px; }
  .brand--front .brand-name { color: var(--ink); font-size: 26px; }
  .brand--front .brand-name small { font-size: 11px; }
  .person { position: absolute; right: 30px; top: 20px; text-align: right; }
  .person-name { color: var(--brand-blue); font-weight: 700; font-size: 28px; letter-spacing: 0.5px; line-height: 1.2; }
  .person-title { color: var(--ink); font-size: 15px; line-height: 1.2; margin-top: 2px; }
  .contact { position: absolute; right: 24px; top: 165px; text-align: right; color: var(--paper); font-size: 14px; line-height: 1.5; font-style: normal; }
  .contact-address { margin-bottom: 8px; }
  .contact-line { display: flex; justify-content: flex-end; align-items: center; gap: 8px; }
  .contact-line svg { width: 12px; height: 12px; flex: none; }
  .web-domain { color: var(--brand-blue-light); }
</style>
</head>
<body>

<section class="card card--back" aria-label="Business card, services side">
  <div class="brand brand--back">
    <span class="brand-dot" aria-hidden="true"></span>
    <p class="brand-name">Corvana<br>Tongue<br>Works <small>LLC</small></p>
  </div>
  <div class="services">
    <div class="rule"></div>
    <ul class="service-list">
      <li>ESL / ENL Language Classes, Private Lessons, and Online Tutors</li>
      <li>PLEXA Training and Testing</li>
      <li>Translating &amp; Interpreting Services</li>
      <li>24/7/365</li>
    </ul>
    <div class="rule"></div>
    <p class="contact-note">Contact us about Over-the-Phone Interpreting in over 200 languages</p>
  </div>
</section>

<section class="card card--front" aria-label="Business card, contact side">
  <svg class="wave" viewBox="0 0 560 320" preserveAspectRatio="none" aria-hidden="true">
    <path d="M0,262 C120,262 190,228 232,170 C275,110 360,90 560,84 L560,90 C365,96 288,118 246,176 C200,240 125,276 0,276 Z" fill="var(--brand-blue)"/>
    <path d="M0,300 C140,298 220,250 265,180 C305,120 370,100 560,96 L560,320 L0,320 Z" fill="var(--ink)"/>
    <path d="M60,320 C170,300 240,250 282,192 C322,134 385,114 560,110" fill="none" stroke="#ffffff" stroke-width="3"/>
  </svg>

  <div class="brand brand--front">
    <span class="brand-dot" aria-hidden="true"></span>
    <p class="brand-name">Corvana<br>Tongue<br>Works <small>LLC</small></p>
  </div>

  <div class="person">
    <p class="person-name">RHODA PELLING</p>
    <p class="person-title">President</p>
  </div>

  <address class="contact">
    <p class="contact-address">482 Garnet Ave., Ste. 219<br>Indianapolis, IN 40917 USA</p>
    <p class="contact-line"><span>(555) 481-3062</span>
      <svg viewBox="0 0 24 24" aria-hidden="true"><path fill="var(--brand-blue-light)" d="M6.6 10.8a15 15 0 0 0 6.6 6.6l2.2-2.2c.3-.3.7-.4 1-.2 1.1.4 2.3.6 3.6.6.6 0 1 .4 1 1V20c0 .6-.4 1-1 1A17 17 0 0 1 3 4c0-.6.4-1 1-1h3.5c.6 0 1 .4 1 1 0 1.3.2 2.5.6 3.6.1.3 0 .7-.2 1z"/></svg>
    </p>
    <p class="contact-line"><span>rmpelling@corvanatongueworks.example</span>
      <svg viewBox="0 0 24 24" aria-hidden="true"><rect x="2" y="5" width="20" height="14" rx="2" fill="none" stroke="var(--brand-blue-light)" stroke-width="2.4"/><path d="M3 6l9 7 9-7" fill="none" stroke="var(--brand-blue-light)" stroke-width="2.4"/></svg>
    </p>
    <p class="contact-line"><span>www.<span class="web-domain">corvanatongue</span>.example</span>
      <svg viewBox="0 0 24 24" aria-hidden="true"><g fill="none" stroke="var(--brand-blue-light)" stroke-width="2"><circle cx="12" cy="12" r="10"/><ellipse cx="12" cy="12" rx="4" ry="10"/><path d="M2 12h20"/></g></svg>
    </p>
  </address>
</section>

</body>
</html>
```